Mental Health Clinic Website

website for a mental health clinic. two files describing the website are attached, in case of conflicting info the word document is priority.

Target Market(s)

Ohio / Pennsylvania residents

Industry/Entity Type

Health Care

Coding

Coded - Design and coding required

Number of Pages Required

5+ page

Requirements
Must have
• see attached

```html
<!DOCTYPE html>
<html lang="en">
<head>
<meta charset="utf-8">
<title>Dr Harlow Serenity Center</title>
<link href="https://fonts.googleapis.com/css2?family=Lato:wght@400;700;900&display=swap" rel="stylesheet">
<style>
:root{
  --blue:#1c5db3;
  --red:#e6312b;
  --orange:#ff6d0a;
  --orange-red:#ff3c3c;
  --green:#4da63a;
  --text:#333;
  --muted:#666;
  --grey-bg:#f0f0f0;
  --yellow:#ffd400;
}
*{box-sizing:border-box;margin:0;padding:0}
html,body{width:1200px;height:4000px;overflow:hidden;background:#fff;font-family:'Lato',sans-serif;color:var(--text)}
.page{position:relative;width:1200px;height:4000px}
section,header,footer{position:absolute;left:0;width:1200px}

/* header */
.site-header{top:0;height:105px}
.brand{position:absolute;left:72px;top:24px;display:flex;align-items:center;gap:14px}
.brand-mark{width:50px;height:50px;border-radius:50%;background:var(--green)}
.brand-name{font-size:25px;font-weight:700;line-height:1.1;color:#222}
.main-nav{position:absolute;right:72px;top:44px;display:flex;gap:46px;font-size:14px;font-weight:700}
.main-nav a{color:#222;text-decoration:none}
.main-nav a.active{color:var(--red)}

/* hero */
.hero{top:105px;height:588px}
.hero-photo{position:absolute;inset:0;background:linear-gradient(100deg,#e6c24a 0%,#c9b065 25%,#8ea24a 55%,#4d6b25 80%,#33501a 100%)}
.hero-title{position:absolute;right:74px;top:232px;text-align:right;color:#fff;font-weight:900;line-height:1.05;text-transform:uppercase}
.hero-title .l1{font-size:30px}
.hero-title .l2{font-size:54px}
.hero-title .l3{font-size:34px}
.hero-dots{position:absolute;left:565px;top:530px;display:flex;gap:8px}
.hero-dots span{width:11px;height:11px;border-radius:50%;background:#fff}
.hero-dots span.on{background:var(--yellow)}

/* welcome */
.welcome{top:693px;height:467px;text-align:center}
.section-title{font-size:34px;font-weight:900;color:var(--blue);text-transform:uppercase;text-align:center}
.welcome .section-title{margin-top:52px}
.welcome p{width:1010px;margin:26px auto 0;font-size:15px;line-height:26px;color:#333}

/* about */
.about{top:1160px;height:395px;background:linear-gradient(90deg,var(--orange),var(--orange-red))}
.about-text{position:absolute;left:75px;top:40px;width:420px;color:#fff}
.about-text h2{font-size:33px;font-weight:900;margin-bottom:18px}
.about-text p{font-size:14.5px;line-height:26px}
.about-text .lang-head{font-weight:700;margin-top:14px}
.lang-list{list-style:none;margin-top:6px}
.lang-list li{font-size:14.5px;line-height:27px;display:flex;align-items:center;gap:18px}
.about-photo{position:absolute;left:527px;top:48px;width:600px;height:287px;background:linear-gradient(180deg,#f4f6f8,#dfe4e8)}

/* team */
.team{top:1555px;height:578px}
.team .section-title{margin-top:56px}
.team-grid{position:absolute;left:80px;top:140px;width:1040px;display:flex;justify-content:space-between}
.member{width:320px;text-align:center}
.member-photo{width:156px;height:156px;border-radius:50%;margin:0 auto;background:linear-gradient(160deg,#d9c3b0,#7b6a5f)}
.member h3{margin-top:30px;font-size:19px;font-weight:900;color:var(--red)}
.member .role{font-size:14px;font-weight:700;color:var(--blue);margin-top:2px}
.member p{font-size:14.5px;line-height:26px;margin-top:4px}
.arrow{position:absolute;top:304px}
.arrow.prev{left:44px}.arrow.next{right:44px}

/* services */
.services{top:2133px;height:640px;background:var(--grey-bg)}
.services .section-title{margin-top:56px}
.service-tabs{position:absolute;left:80px;top:112px;width:1030px;display:flex}
.tab{width:206px;height:172px;text-align:center;padding-top:16px}
.tab.active{background:#fff}
.tab-icon{width:90px;height:90px;border-radius:50%;margin:0 auto;background:#fff;display:flex;align-items:center;justify-content:center}
.tab.active .tab-icon{border:3px solid var(--red)}
.tab-icon span{width:50px;height:50px;border-radius:50%;background:#9a9a9a}
.tab.active .tab-icon span{background:var(--green)}
.tab h4{margin-top:10px;font-size:14px;font-weight:900;color:var(--blue);text-transform:uppercase;line-height:18px}
.tab.active h4{color:var(--red)}
.tab small{display:block;font-size:13px;font-weight:700;color:var(--blue);line-height:16px}
.service-panel{position:absolute;left:80px;top:284px;width:1050px;height:310px;background:#fff}
.service-photo{position:absolute;left:17px;top:44px;width:400px;height:224px;background:linear-gradient(120deg,#d7dde2,#7d8fa0 60%,#3e4c5c)}
.service-body{position:absolute;left:445px;top:40px;width:560px}
.service-body h3{font-size:22px;font-weight:900;color:var(--red)}
.service-body p{font-size:14.5px;line-height:26px;margin-top:8px}
.btn{display:inline-block;font-weight:700;font-size:16px;text-align:center}
.btn-green{margin-top:16px;background:var(--green);color:#fff;padding:11px 30px}

/* good reads */
.reads{top:2773px;height:560px}
.reads .section-title{margin-top:50px}
.read-grid{position:absolute;left:75px;top:123px;width:1050px;display:flex;justify-content:space-between}
.read{width:512px}
.read-photo{height:208px;background:linear-gradient(120deg,#e7ddd6,#a88a7a 50%,#3a2e2a)}
.read:nth-child(2) .read-photo{background:linear-gradient(90deg,#5a3a28,#c9a57a 45%,#efe6dc 70%,#8a5f44)}
.read h3{margin-top:22px;font-size:22px;font-weight:900;color:var(--red);text-transform:uppercase}
.author{display:flex;align-items:center;gap:12px;margin-top:10px;font-size:13px;font-weight:900;color:var(--green);text-transform:uppercase}
.read p{margin-top:14px;font-size:14.5px;line-height:26px}

/* contact */
.contact{top:3333px;height:502px}
.map{position:absolute;left:0;top:0;width:512px;height:502px;background:linear-gradient(160deg,#eceae4,#dcdad2)}
.contact-card{position:absolute;left:75px;top:50px;width:412px;height:157px;background:#fff;padding:14px 22px}
.contact-card h2{font-size:33px;font-weight:900;color:var(--blue)}
.contact-card ul{list-style:none;margin-top:8px}
.contact-card li{display:flex;align-items:center;gap:18px;font-size:14px;line-height:25px}
.pin{position:absolute;left:224px;top:218px}
.appointment{position:absolute;left:512px;top:0;width:688px;height:502px;background:linear-gradient(135deg,#5aa535 0%,#2f8a6a 45%,#1f5fb0 100%);padding:40px 38px;color:#fff}
.appointment h2{font-size:34px;font-weight:700;text-transform:uppercase}
.field{width:585px;height:44px;background:#fff;margin-top:12px;color:#222;font-weight:700;font-size:14px;line-height:44px;padding-left:14px}
.appointment h2+.field{margin-top:32px}
.appointment p{margin-top:18px;font-size:16px}
.btn-yellow{margin-top:16px;background:var(--yellow);color:#222;padding:10px 46px}

/* footer */
.site-footer{top:3835px;height:165px;text-align:center}
.foot-nav{margin-top:46px;display:flex;justify-content:center;gap:44px;font-size:13px;font-weight:700}
.copyright{margin-top:16px;font-size:12px;color:#444}
.social{display:flex;justify-content:center;gap:18px;margin-top:16px}
.social span{width:18px;height:18px;border-radius:50%;background:#222}
</style>
</head>
<body>
<div class="page">

<header class="site-header">
  <div class="brand"><span class="brand-mark"></span><span class="brand-name">Dr Harlow<br>Serenity Center</span></div>
  <nav class="main-nav"><a class="active">HOME</a><a>ABOUT US</a><a>SERVICES</a><a>GOOD READS</a><a>CONTACT</a></nav>
</header>

<section class="hero">
  <div class="hero-photo" role="img" aria-label="Woman relaxing outdoors in warm sunlight"></div>
  <h1 class="hero-title"><span class="l1">Welcome to</span><br><span class="l2">Dr Harlow</span><br><span class="l3">Serenity Center</span></h1>
  <div class="hero-dots"><span></span><span class="on"></span><span></span><span></span></div>
</section>

<section class="welcome">
  <h2 class="section-title">Welcome to our website</h2>
  <p>Each individual is unique with unique personality and unique needs. Therefore we provide individual treatment customized for you or your child. Multiculturalism also informs our practice. We are a full service mental health practice with the capacity to serve adults, children, teens and their parents.</p>
  <p>We provide high quality evidence based treatment and care including medication management, pharmacogenomic testing, individual psychotherapy, group psychotherapy, art therapy, CBT, DBT and trauma therapy. Our providers are experts in treating variety of illnesses such as depression, anxiety, schizophrenia, ADHD, gender identity concerns and PTSD.</p>
  <p>We are experienced in a variety of methods that help people achieve their psychological goals, and we will discuss with you the best ways to attain the health and wellness that you deserve. We are committed to helping you achieve your optimal level of emotional functioning and fulfill a successful life.</p>
</section>

<section class="about">
  <div class="about-text">
    <h2>ABOUT US</h2>
    <p>You will find a number of highly specialized – experienced and caring therapists and psychiatrists in Serenity Center. We provide medication management and psychotherapy (counseling) across the lifespan, – children, teens and adults.</p>
    <p class="lang-head">Other than English, we speak the following languages</p>
    <ul class="lang-list">
      <li><svg width="14" height="12" viewBox="0 0 14 12"><path d="M1 6l4 4 8-9" fill="none" stroke="#fff" stroke-width="2.5"/></svg>Spanish</li>
      <li><svg width="14" height="12" viewBox="0 0 14 12"><path d="M1 6l4 4 8-9" fill="none" stroke="#fff" stroke-width="2.5"/></svg>German</li>
      <li><svg width="14" height="12" viewBox="0 0 14 12"><path d="M1 6l4 4 8-9" fill="none" stroke="#fff" stroke-width="2.5"/></svg>Farsi</li>
      <li><svg width="14" height="12" viewBox="0 0 14 12"><path d="M1 6l4 4 8-9" fill="none" stroke="#fff" stroke-width="2.5"/></svg>Hebrew</li>
    </ul>
  </div>
  <div class="about-photo" role="img" aria-label="Woman meditating in a bright white room"></div>
</section>

<section class="team">
  <h2 class="section-title">Meet the team</h2>
  <svg class="arrow prev" width="16" height="26" viewBox="0 0 16 26"><path d="M13 2L3 13l10 11" fill="none" stroke="#555" stroke-width="3"/></svg>
  <svg class="arrow next" width="16" height="26" viewBox="0 0 16 26"><path d="M3 2l10 11L3 24" fill="none" stroke="#555" stroke-width="3"/></svg>
  <div class="team-grid">
    <div class="member"><div class="member-photo" role="img" aria-label="Portrait of team member"></div><h3>NAME HEADING</h3><div class="role">Partner</div><p>Lorem ipsum dolor sit amet, consectetur adipiscing elit. Cras ullamcorper elit in ligula dignissim, vel consequat ante ullamcorper. Nullam sollicitudin orci et justo malesuada, vel ullamcorper augue vestibulum..</p></div>
    <div class="member"><div class="member-photo" role="img" aria-label="Portrait of team member"></div><h3>NAME HEADING</h3><div class="role">Partner</div><p>Lorem ipsum dolor sit amet, consectetur adipiscing elit. Cras ullamcorper elit in ligula dignissim, vel consequat ante ullamcorper. Nullam sollicitudin orci et justo malesuada, vel ullamcorper augue vestibulum..</p></div>
    <div class="member"><div class="member-photo" role="img" aria-label="Portrait of team member"></div><h3>NAME HEADING</h3><div class="role">Partner</div><p>Lorem ipsum dolor sit amet, consectetur adipiscing elit. Cras ullamcorper elit in ligula dignissim, vel consequat ante ullamcorper. Nullam sollicitudin orci et justo malesuada, vel ullamcorper augue vestibulum..</p></div>
  </div>
</section>

<section class="services">
  <h2 class="section-title">Our services</h2>
  <div class="service-tabs">
    <div class="tab active"><div class="tab-icon" role="img" aria-label="Medication icon"><span></span></div><h4>Medication<br>Management</h4></div>
    <div class="tab"><div class="tab-icon" role="img" aria-label="Psychotherapy icon"><span></span></div><h4>Psychotherapy</h4><small>Individual, group, couples,<br>and family</small></div>
    <div class="tab"><div class="tab-icon" role="img" aria-label="Art therapy icon"><span></span></div><h4>Art<br>Therapy</h4></div>
    <div class="tab"><div class="tab-icon" role="img" aria-label="Treatment approach icon"><span></span></div><h4>Treatment<br>Approach</h4></div>
    <div class="tab"><div class="tab-icon" role="img" aria-label="Treatment areas icon"><span></span></div><h4>Treatment<br>Areas</h4></div>
  </div>
  <div class="service-panel">
    <div class="service-photo" role="img" aria-label="Man reading a medication label"></div>
    <div class="service-body">
      <h3>MEDICATION MANAGEMENT</h3>
      <p>Lorem ipsum dolor sit amet, consectetur adipiscing elit. Cras ullamcorper elit in ligula dignissim, vel consequat ante ullamcorper. Nullam sollicitudin orci et justo malesuada, vel ullamcorper augue vestibulum vivamus tempus lobortis elit, a imperdiet orci ultrices dignissim. Curabitur eros neque, sagittis at interdum eget, lactus eget mauris.</p>
      <span class="btn btn-green">Read More</span>
    </div>
  </div>
</section>

<section class="reads">
  <h2 class="section-title">Good reads</h2>
  <div class="read-grid">
    <article class="read"><div class="read-photo" role="img" aria-label="Woman reading a book"></div><h3>Duis nec lacus ac nibh</h3><div class="author"><svg width="12" height="13" viewBox="0 0 12 13"><circle cx="6" cy="3.5" r="3" fill="#4da63a"/><path d="M0 13c0-4 2.5-6 6-6s6 2 6 6z" fill="#4da63a"/></svg>Author name</div><p>Lorem ipsum dolor sit amet, consectetur adipiscing elit. Cras ullamcorper elit in ligula dignissim, vel consequat ante ullamcorper. Nullam sollicitudin orci et justo malesuada, vel ullamcorper augue vestibulum.</p></article>
    <article class="read"><div class="read-photo" role="img" aria-label="Row of books on a shelf"></div><h3>Duis nec lacus ac nibh</h3><div class="author"><svg width="12" height="13" viewBox="0 0 12 13"><circle cx="6" cy="3.5" r="3" fill="#4da63a"/><path d="M0 13c0-4 2.5-6 6-6s6 2 6 6z" fill="#4da63a"/></svg>Author name</div><p>Lorem ipsum dolor sit amet, consectetur adipiscing elit. Cras ullamcorper elit in ligula dignissim, vel consequat ante ullamcorper. Nullam sollicitudin orci et justo malesuada, vel ullamcorper augue vestibulum.</p></article>
  </div>
</section>

<section class="contact">
  <div class="map" role="img" aria-label="Street map around the clinic"></div>
  <svg class="pin" width="26" height="36" viewBox="0 0 26 36"><path d="M13 0C6 0 0 6 0 13c0 9 13 23 13 23s13-14 13-23C26 6 20 0 13 0z" fill="#d93a2b"/><circle cx="13" cy="13" r="4.5" fill="#8a1e14"/></svg>
  <div class="contact-card">
    <h2>CONTACT US</h2>
    <ul>
      <li><svg width="12" height="16" viewBox="0 0 12 16"><path d="M6 0C2.7 0 0 2.7 0 6c0 4.5 6 10 6 10s6-5.5 6-10C12 2.7 9.3 0 6 0z" fill="#222"/><circle cx="6" cy="6" r="2.2" fill="#fff"/></svg>4820 Maple Ridge Road, Suite 210, Aurora, OH 44202</li>
      <li><svg width="14" height="14" viewBox="0 0 14 14"><path d="M3 0l3 3-2 2c1 2 3 4 5 5l2-2 3 3-2 3C6 14 0 8 0 2z" fill="#222"/></svg>(440) 555-0192</li>
      <li><svg width="14" height="11" viewBox="0 0 14 11"><rect width="14" height="11" fill="#222"/><path d="M0 1l7 5 7-5" fill="none" stroke="#fff" stroke-width="1.2"/></svg>dr.harlow@harlowserenity.com</li>
    </ul>
  </div>
  <div class="appointment">
    <h2>Appointment request</h2>
    <div class="field">First Name</div>
    <div class="field">Last Name</div>
    <div class="field">Email Address</div>
    <div class="field">Phone No</div>
    <p>Please contact me for an appointment</p>
    <span class="btn btn-yellow">Read More</span>
  </div>
</section>

<footer class="site-footer">
  <nav class="foot-nav"><a>HOME</a><a>ABOUT US</a><a>SERVICES</a><a>GOOD READS</a><a>CONTACT</a></nav>
  <p class="copyright">Copyright © 2019 . Company Name All Right Reserved</p>
  <div class="social"><span></span><span></span><span></span><span></span><span></span><span></span></div>
</footer>

</div>
</body>
</html>
```